SOLVE Study flyer

I need help designing a flyer for a research study that will include brain imaging in adolescents. The info is in the attached document. The study is called the Sequoia Outlook Lantern Valley Echo (SOLVE) study. Ideally this would be returned as a document that I can edit in the future as we will have several new recruitment phases (different age groups, etc. I also would love to have a logo designed as part of this project, but I recognize that might be a separate design request.

```html
<!DOCTYPE html>
<html lang="en">
<head>
<meta charset="UTF-8">
<title>SOLVE Study Flyer</title>
<link href="https://fonts.googleapis.com/css2?family=Bebas+Neue&family=Poppins:wght@500;600;700&family=Alegreya+SC:ital,wght@1,700&display=swap" rel="stylesheet">
<style>
  :root {
    --plum: #7a176f;
    --plum-deep: #5e0f56;
    --orchid: #f9a6f6;
    --orchid-bright: #f287ee;
    --orchid-light: #fbb6f8;
    --backdrop: #b9b9b9;
    --paper: #ffffff;
    --ink: #2a0a26;
  }
  * { margin: 0; padding: 0; box-sizing: border-box; }
  html, body { width: 984px; height: 1200px; overflow: hidden; background: var(--backdrop); }
  body { position: relative; font-family: "Poppins", sans-serif; }

  .flyer {
    position: absolute; left: 160px; top: 102px; width: 663px; height: 995px;
    background: var(--paper); overflow: hidden;
  }
  .hero { position: absolute; left: 0; top: 0; width: 663px; height: 452px; background: var(--plum); }

  .study-title {
    position: absolute; left: 27px; top: 20px;
    font-family: "Bebas Neue", sans-serif; color: var(--paper);
    font-size: 27px; line-height: 29px; letter-spacing: 0.2px;
  }
  .study-title .accent { display: block; color: var(--orchid-light); letter-spacing: 2.2px; }

  .headline {
    position: absolute; left: 27px; color: var(--paper);
    font-weight: 700; font-size: 37px; line-height: 43px; letter-spacing: -0.3px;
  }
  .headline.ask { top: 110px; }
  .headline.worry { top: 298px; line-height: 41px; }

  .age-tag {
    position: absolute; left: 27px; top: 220px; width: 220px; height: 60px;
    background: var(--orchid-bright); border-top-right-radius: 50px 60px;
    color: var(--plum); font-weight: 700; font-size: 33px; line-height: 60px; padding-left: 16px;
  }
  .doodle { position: absolute; left: 240px; top: 200px; }

  .photo {
    position: absolute; left: 354px; top: 106px; width: 284px; height: 284px; border-radius: 50%;
    background: radial-gradient(circle at 45% 40%, #c9a087 0%, #8fb3a2 38%, #3a3a3a 75%, #262626 100%);
  }

  .intro {
    position: absolute; left: 20px; top: 476px; width: 623px; text-align: center;
    color: var(--plum); font-weight: 700; font-size: 15.5px; line-height: 27.5px; text-transform: uppercase;
  }

  .section-pill {
    position: absolute; left: 158px; top: 565px; width: 347px; height: 37px;
    background: var(--plum); color: var(--paper); text-align: center;
    font-weight: 700; font-size: 18px; line-height: 37px; letter-spacing: 0.2px;
  }
  .section-pill::before, .section-pill::after {
    content: ""; position: absolute; top: -3px; width: 8px; height: 43px; border-radius: 4px; background: var(--plum);
  }
  .section-pill::before { left: -1px; }
  .section-pill::after { right: -1px; }

  .involves { position: absolute; left: 94px; top: 614px; width: 500px; list-style: none; }
  .involves li {
    position: relative; padding-left: 15px; margin-bottom: 13px;
    font-weight: 500; font-size: 11.8px; line-height: 16px; color: var(--ink);
  }
  .involves svg { position: absolute; left: -1px; top: 1px; }

  .eligibility {
    position: absolute; left: 27px; top: 756px; width: 611px; height: 152px;
    background: var(--orchid); border-bottom-left-radius: 52px;
  }
  .eligibility h2 {
    position: absolute; left: 63px; top: 16px;
    color: var(--plum-deep); font-weight: 600; font-size: 27px; letter-spacing: -0.2px;
  }
  .criteria { position: absolute; left: 69px; top: 56px; list-style: none; }
  .criteria li {
    position: relative; padding-left: 22px; height: 30px;
    font-weight: 500; font-size: 12px; line-height: 18px; color: var(--ink);
  }
  .criteria svg { position: absolute; left: 0; top: 1px; }

  .contact-call {
    position: absolute; left: 0; top: 921px; width: 663px; text-align: center; white-space: nowrap;
    font-size: 16px; color: var(--ink);
  }
  .contact-call .serif { font-family: "Alegreya SC", serif; font-style: italic; font-weight: 700; }
  .contact-call .lead { color: var(--plum); font-weight: 700; font-size: 18px; }

  .footer-band {
    position: absolute; left: 0; top: 964px; width: 663px; height: 31px; background: var(--plum);
    color: var(--paper);
  }
  .footer-band .email { position: absolute; left: 28px; top: 0; font-size: 15px; line-height: 31px; }
  .footer-band .pay { position: absolute; right: 25px; top: 0; font-weight: 700; font-size: 20px; line-height: 31px; }
</style>
</head>
<body>
<main class="flyer">
  <section class="hero">
    <h1 class="study-title">Sequoia Outlook Lantern<span class="accent">Valley Echo</span></h1>
    <p class="headline ask">Are you the<br>Parent&nbsp; of a Child</p>
    <p class="age-tag">Age 10-17?</p>
    <svg class="doodle" width="120" height="70" viewBox="0 0 120 70" aria-hidden="true">
      <path d="M10 62 C30 55 28 30 38 18 C48 5 75 5 88 15 C98 24 90 38 84 28 C78 18 96 8 112 26"
            fill="none" stroke="#ffffff" stroke-width="1.2" stroke-dasharray="2.5 2.5"/>
      <path d="M16 57 L9 62 L17 64" fill="none" stroke="#ffffff" stroke-width="1.4"/>
    </svg>
    <p class="headline worry">Do they worry or<br>overthink negative<br>emotions?</p>
    <div class="photo" role="img" aria-label="Photo of a young woman with long wavy hair crafting with clay at a table"></div>
  </section>

  <p class="intro">Northvale University researchers are seeking girls age 10-17 for<br>a study about brain activity in emotions and decision-making and<br>how they relate to puberty, anxiety and depression.</p>

  <div class="section-pill">STUDY PARTICIPATION INVOLVES</div>

  <ul class="involves">
    <li><svg width="16" height="14" viewBox="0 0 16 14" aria-hidden="true"><path d="M7 1 L13 7 L7 13 L1 7 Z" fill="none" stroke="#7a176f" stroke-width="1"/><path d="M7 4.5 L9.5 7 L7 9.5 L4.5 7 Z" fill="#7a176f"/><path d="M10 1 L16 7 L10 13" fill="none" stroke="#7a176f" stroke-width="1"/></svg>One one-hour interview (online or in-person) where your child will discuss their thoughts</li>
    <li><svg width="16" height="14" viewBox="0 0 16 14" aria-hidden="true"><path d="M7 1 L13 7 L7 13 L1 7 Z" fill="none" stroke="#7a176f" stroke-width="1"/><path d="M7 4.5 L9.5 7 L7 9.5 L4.5 7 Z" fill="#7a176f"/><path d="M10 1 L16 7 L10 13" fill="none" stroke="#7a176f" stroke-width="1"/></svg>Online questionnaires (parent and child)</li>
    <li><svg width="16" height="14" viewBox="0 0 16 14" aria-hidden="true"><path d="M7 1 L13 7 L7 13 L1 7 Z" fill="none" stroke="#7a176f" stroke-width="1"/><path d="M7 4.5 L9.5 7 L7 9.5 L4.5 7 Z" fill="#7a176f"/><path d="M10 1 L16 7 L10 13" fill="none" stroke="#7a176f" stroke-width="1"/></svg>One two-hour visit where your child will complete an MRI scan, answer questions about their puberty stage, and have a small hair sample taken to study puberty hormones</li>
  </ul>

  <section class="eligibility">
    <h2>YOUR CHILD MAY BE ELIGIBLE IF THEY</h2>
    <ul class="criteria">
      <li><svg width="17" height="17" viewBox="0 0 17 17" aria-hidden="true"><circle cx="8" cy="9" r="7" fill="none" stroke="#7a176f" stroke-width="1.4"/><path d="M4.5 8.5 L7.5 11.5 L15.5 2" fill="none" stroke="#7a176f" stroke-width="1.8"/></svg>Are age 10-17</li>
      <li><svg width="17" height="17" viewBox="0 0 17 17" aria-hidden="true"><circle cx="8" cy="9" r="7" fill="none" stroke="#7a176f" stroke-width="1.4"/><path d="M4.5 8.5 L7.5 11.5 L15.5 2" fill="none" stroke="#7a176f" stroke-width="1.8"/></svg>Tend to worry or overthink negative thoughts</li>
      <li><svg width="17" height="17" viewBox="0 0 17 17" aria-hidden="true"><circle cx="8" cy="9" r="7" fill="none" stroke="#7a176f" stroke-width="1.4"/><path d="M4.5 8.5 L7.5 11.5 L15.5 2" fill="none" stroke="#7a176f" stroke-width="1.8"/></svg>Have not been diagnosed with psychosis, learning problems, or autism</li>
    </ul>
  </section>

  <p class="contact-call"><span class="serif">Interested in participating?</span> <span class="lead">Want more information?</span> <span class="serif">Please contact us!</span></p>

  <footer class="footer-band">
    <span class="email">solvestudy@northvale.edu</span>
    <span class="pay">Compensation up to $140</span>
  </footer>
</main>
</body>
</html>
```